Brindle Healthcare Coming Soon Sign

I need a large (10 x5) road banner announcing the construction of our new medical practice at 5187 Larkmoor Road in John's Island. The name of our practice is Brindle Healthcare and we thought it would be fund to nick name it the "Brindle Waystation". We'd like the tagline to read - "There's nothing healthy about driving an hour to see your doctor. So we're coming to you." Opening Late 2025 I have attached three logos as we have two other practices (Brindle Urgent and Brindle Aesthetics ) that should be present on the bottom of the sign but the main business is Brindle Healthcare. For more information on our look/feel visit our website www.goplainway-example.com (which should be somewhere on the banner as well)
Updates

The signage needs to say Coming Late Fall 2025!

Target Market(s)

Drive By traffic must be made aware that we are coming soon

Industry/Entity Type

Healthcare

Requirements
Nice to have
• Western Theme

```html
<!DOCTYPE html>
<html lang="en">
<head>
<meta charset="utf-8">
<title>Brindle Healthcare – Coming Soon Road Banner</title>
<link rel="stylesheet" href="https://fonts.googleapis.com/css2?family=Roboto:wght@500;700&display=swap">
<style>
  :root {
    --navy: #22335e;
    --navy-edge: #1b2a4f;
    --white: #ffffff;
    --sky: #5aa9e0;
    --arrow: #2fa8e6;
    --rose: #e8186d;
    --backdrop: #e9ecf1;
  }
  * { margin: 0; padding: 0; box-sizing: border-box; }
  html, body {
    width: 1200px;
    height: 798px;
    overflow: hidden;
    background: var(--backdrop);
    font-family: "Roboto", Arial, sans-serif;
  }
  .banner-frame {
    position: absolute;
    left: 30px;
    top: 108px;
    width: 1140px;
    height: 582px;
    background: var(--white);
    border: 2px solid var(--navy-edge);
    padding: 9px;
  }
  .banner {
    position: relative;
    width: 100%;
    height: 100%;
    background: var(--navy);
    color: var(--white);
  }
  .brand {
    position: absolute;
    left: 42px;
    top: 54px;
    display: flex;
    align-items: center;
    gap: 16px;
  }
  .brand-dot {
    width: 58px;
    height: 58px;
    border-radius: 50%;
    background: var(--sky);
  }
  .brand-name {
    font-weight: 700;
    font-size: 40px;
    letter-spacing: 2px;
    color: var(--white);
  }
  .opening {
    position: absolute;
    right: 45px;
    top: 46px;
    font-weight: 500;
    font-size: 39px;
    color: var(--sky);
  }
  .tagline {
    position: absolute;
    left: 42px;
    top: 218px;
    font-weight: 500;
    font-size: 41px;
    line-height: 59px;
  }
  .contact {
    position: absolute;
    left: 42px;
    top: 446px;
    list-style: none;
    font-weight: 500;
    font-size: 24px;
  }
  .contact li {
    display: flex;
    align-items: center;
    gap: 12px;
    height: 45px;
  }
  .contact svg { width: 30px; height: 30px; }
  .chevrons {
    position: absolute;
    left: 505px;
    top: 476px;
  }
  .sister-practices {
    position: absolute;
    right: 45px;
    top: 474px;
    display: flex;
    align-items: center;
    gap: 26px;
    font-weight: 700;
  }
  .sister {
    font-size: 24px;
    letter-spacing: 1px;
    white-space: nowrap;
  }
  .sister--aesthetics { color: var(--rose); }
  .sister--urgent { color: var(--white); }
</style>
</head>
<body>
  <div class="banner-frame">
    <section class="banner">
      <header>
        <div class="brand">
          <span class="brand-dot"></span>
          <span class="brand-name">Brindle Healthcare</span>
        </div>
        <p class="opening">Coming Late Fall 2025!</p>
      </header>

      <h1 class="tagline">There's Nothing Healthy About Driving An<br>Hour To See Your Doctor. So We're Coming To You.</h1>

      <ul class="contact">
        <li>
          <svg viewBox="0 0 24 24" aria-hidden="true"><path d="M12 2a7 7 0 0 0-7 7c0 5 7 13 7 13s7-8 7-13a7 7 0 0 0-7-7zm0 9.5A2.5 2.5 0 1 1 12 6.5a2.5 2.5 0 0 1 0 5z" fill="#fff"/></svg>
          <span>5187 Larkmoor Road in John's Island</span>
        </li>
        <li>
          <svg viewBox="0 0 24 24" aria-hidden="true" fill="none" stroke="#fff" stroke-width="1.6"><circle cx="12" cy="12" r="10"/><ellipse cx="12" cy="12" rx="4.5" ry="10"/><path d="M2 12h20M4 6.5h16M4 17.5h16"/></svg>
          <span>www.goplainway-example.com</span>
        </li>
      </ul>

      <svg class="chevrons" width="76" height="34" viewBox="0 0 76 34" aria-hidden="true">
        <g fill="var(--arrow)">
          <path d="M0 2l14 15L0 32z"/>
          <path d="M20 2l14 15-14 15z"/>
          <path d="M40 2l14 15-14 15z"/>
          <path d="M60 2l14 15-14 15z"/>
        </g>
      </svg>

      <div class="sister-practices">
        <span class="sister sister--aesthetics">Brindle Aesthetics</span>
        <span class="sister sister--urgent">Brindle Urgent</span>
      </div>
    </section>
  </div>
</body>
</html>
```